We need a modern WIX website for Brightform Beam Services Australia (Laser/Industrial/Engineering)

We need a website for Wix (coded) for our laser restoration and industrial cleaning business.

It will need to be 4-6 pages.
Pages may include:
Home
About
Why Laser
Capabilities
There needs to be a contact / quote form

We do not want boring institutional design, so please do try to be a little creative (but not artsy, more engineering / laser etc). We hesitate with boxy wordpress looking templates, so please bring in strip backgrounds and sliders etc;

Our brand colours are blue and red, but a sharp modern site relative to the industry and work is important.

We envision the home page to take visitors on a informed journey of who, what, why, how, explaining the capability of laser science across contaminants, industries and surfaces.

We envision the home page to be strips:
- landing
- intro

-Why choose laser / What is laser cleaning
Minimum downtime, no surface damage, no environmental impact, no mess, no waste, complete restoration (we have an explainer video)

- Contaminants
Bacteria, Rust, Corrosion, Oxides, Grease, Oil, Paint, Stains, Mold, Soot / Carbon, Graffiti, Coatings, Dirt, Residue

- Surfaces
Metals, Engines/Parts/Components, Tools, Machinery, Bricks/Blockwork, Concrete, Paint, Stone, Wood, Aluminium

- Industries
Medical/Sterile, Hospitality, Bio Hazardous, Construction, Infrastructure, Property, Industrial, Engineer, Automotive, Marine, Heritage, Non Destructive Testing,

----
Here is some info on the company below:

"Background Information - Brightform Beam Services Australia (BBSA) is a leading provider of advanced laser restoration services for the residential, commercial, medical, hazardous and industrial sectors, offering waste free, chemical free and damage free complete restoration of metals, concrete, wood, stone and heritage, hygiene and hazard surfaces, with complete removal of coatings, bacteria, paint, rust, graffiti, mold and fire ash (soot), and preparation and treating for welding and bonding.
Servicing Melbourne and Victoria, with additional services available Australia wide, BBSA offers a 24/7 call-out service to your site.
With no downtime to your operations, we offer a timely resolution to your cleaning and maintenance needs."

We have attached some inspiration of websites we like the flow/feel of, but feel free to put your best designs forward.

You are welcome to use dummy headers and text at this stage, as design and feel is most important, and we can add text later.

```html
<!DOCTYPE html>
<html lang="en">
<head>
<meta charset="utf-8">
<title>Brightform Beam Services Australia</title>
<link rel="stylesheet" href="https://fonts.googleapis.com/css2?family=Montserrat:wght@400;500;600;700;800&display=swap">
<style>
:root{
  --red:#e8262f;
  --blue:#1a6fc4;
  --black:#050505;
  --panel:#111216;
  --dark:#16171b;
  --white:#ffffff;
  --muted:#cfd2d8;
  --outline:rgba(255,255,255,.35);
}
*{margin:0;padding:0;box-sizing:border-box}
html,body{width:1200px;height:4243px;overflow:hidden;background:var(--black);font-family:'Montserrat',sans-serif;color:var(--white)}
.page{position:relative;width:1200px;height:4243px;overflow:hidden}
.abs{position:absolute}
a{color:inherit;text-decoration:none}

/* header */
.topbar{left:354px;top:0;width:846px;height:40px;background:var(--red);clip-path:polygon(0 0,100% 0,100% 100%,12px 100%)}
.topbar-item{top:10px;font-size:14px;font-weight:500;display:flex;align-items:center;gap:10px}
.topbar-item .ico{width:22px;height:22px;border-radius:50%;background:var(--blue);display:flex;align-items:center;justify-content:center}
.search{left:895px;top:9px;width:198px;height:26px;background:#fff;border-radius:13px;color:#666;font-size:11px;padding:6px 10px}
.search .btn{position:absolute;right:3px;top:3px;width:20px;height:20px;border-radius:50%;background:var(--red)}
.logo{left:112px;top:34px;display:flex;align-items:center;gap:12px;font-weight:800;font-size:52px;letter-spacing:2px;color:var(--white);line-height:1}
.logo .mark{width:14px;height:14px;background:var(--red)}
.nav{top:72px;font-size:14px;font-weight:500}
.quote{left:974px;top:63px;width:122px;height:33px;border-radius:4px;background:linear-gradient(90deg,var(--blue),var(--red));font-size:14px;font-weight:700;display:flex;align-items:center;justify-content:center}

/* hero */
.hero-photo{left:0;top:125px;width:1200px;height:675px;background:
 radial-gradient(ellipse 320px 220px at 760px 580px,rgba(255,160,60,.55),transparent 70%),
 radial-gradient(ellipse 500px 400px at 700px 300px,rgba(40,90,160,.55),transparent 70%),
 linear-gradient(180deg,#0d1a2e 0%,#14243c 50%,#0a0f18 100%)}
.hero-title{left:102px;top:264px;font-size:39px;font-weight:700;line-height:46px;letter-spacing:.5px}
.hero-text{left:102px;top:410px;width:400px;font-size:14px;line-height:22px;color:#e9ecf1}
.btn-grad{display:flex;align-items:center;justify-content:center;font-weight:700;font-size:14px;border-radius:3px;background:linear-gradient(90deg,var(--blue),var(--red))}
.hero-btn{left:102px;top:491px;width:120px;height:33px}
.hero-cut{left:0;top:620px}

/* headings */
.sec-title{width:1200px;left:0;text-align:center;font-weight:700;font-size:30px;letter-spacing:.5px}
.sec-dot{width:8px;height:8px;border-radius:50%;background:#fff}
.vert{font-weight:700;color:transparent;-webkit-text-stroke:1.2px var(--outline);letter-spacing:2px;line-height:1;white-space:nowrap;transform-origin:0 0}
.vert.down{writing-mode:vertical-rl}
.vert.up{writing-mode:vertical-rl;transform:rotate(180deg)}

/* why */
.why-card{top:1008px;width:224px;height:154px;background:#fff;color:#111;display:flex;flex-direction:column;align-items:center;padding-top:22px;text-align:center}
.why-card h3{font-size:19px;font-weight:700;line-height:22px;margin-top:14px}
.why-card.active{top:964px;height:242px;background:linear-gradient(180deg,var(--blue),var(--red));color:#fff;padding:22px 20px 0}
.why-card.active h3{margin-top:14px}
.why-card.active p{font-size:11px;line-height:18px;margin-top:10px;color:#f1f1f1}
.icon-ring{width:54px;height:54px}

/* about */
.about-bg{left:0;top:1302px;width:1200px;height:659px;background:radial-gradient(ellipse 600px 400px at 900px 500px,#1e2026,transparent),linear-gradient(160deg,#1b1c21,#0e0f12)}
.about-frame-blue{left:100px;top:1407px;width:242px;height:078px;border-left:4px solid var(--blue);border-top:4px solid var(--blue);height:078px}
.about-frame-red{left:420px;top:1700px;width:137px;height:133px;border-right:4px solid var(--red);border-bottom:4px solid var(--red)}
.about-photo{left:119px;top:1421px;width:425px;height:412px;background:linear-gradient(180deg,#3d4652 0%,#6b5a3e 45%,#8c3a25 75%,#3b3b40 100%)}
.about-title{left:640px;top:1432px;font-size:30px;font-weight:700;line-height:38px}
.about-text{left:640px;top:1520px;width:455px;font-size:14.5px;line-height:25.6px;color:var(--muted)}
.about-btn{left:640px;top:1765px;width:123px;height:33px}

/* contaminants */
.cont-bg{left:0;top:1961px;width:1200px;height:514px;background:radial-gradient(ellipse 500px 300px at 200px 120px,rgba(90,60,20,.35),transparent),linear-gradient(180deg,#141518,#0c0d10)}
.hex{clip-path:polygon(50% 0,100% 25%,100% 75%,50% 100%,0 75%,0 25%)}
.cont-hex{top:2142px;width:198px;height:218px;background:#d8d8d8}
.cont-hex .inner{position:absolute;left:4px;top:4px;width:190px;height:210px}
.cont-label{top:2374px;width:240px;text-align:center;font-size:20px;font-weight:700}
.arrow{width:18px;height:18px;border-radius:50%;background:#fff;display:flex;align-items:center;justify-content:center}

/* surfaces */
.surf-title{left:102px;top:2606px;font-size:30px;font-weight:700}
.view-more{left:976px;top:2614px;width:123px;height:36px;border:1.5px solid var(--red);border-radius:3px;font-size:14px;font-weight:700;display:flex;align-items:center;justify-content:center}
.surf-card{top:2686px;height:368px;border-radius:0 26px 0 26px}
.surf-label{top:3084px;font-size:19px;font-weight:700;display:flex;align-items:center;gap:8px;justify-content:center}
.surf-line{top:3132px;height:2px;background:#5a5b60}

/* industries */
.ind-bg{left:0;top:3230px;width:1200px;height:620px;background:radial-gradient(ellipse 500px 300px at 600px 200px,#1c1d22,transparent),#0d0e11}
.ind-hex{top:3444px;width:118px;height:134px;background:#d9d9d9}
.ind-hex .inner{position:absolute;left:2px;top:2px;width:114px;height:130px;background:#0d0e11;display:flex;align-items:center;justify-content:center}
.ind-label{top:3612px;width:200px;text-align:center;font-size:16px;font-weight:700}

/* footer */
.foot-bg{left:0;top:3775px;width:1200px;height:468px;background:linear-gradient(180deg,#1a1c22 0%,#22252d 60%,#121318 100%)}
.foot-logo{left:0;width:1200px;top:3895px;text-align:center;font-size:76px;font-weight:800;letter-spacing:4px;line-height:1}
.foot-nav{left:0;width:1200px;top:4026px;display:flex;justify-content:center;gap:28px;font-size:17px;font-weight:500}
.foot-nav span.sep{color:#cfd2d8}
.social{top:4088px;width:24px;height:24px;border-radius:50%;background:linear-gradient(135deg,var(--blue),var(--red))}
.copy{left:0;width:1200px;top:4180px;text-align:center;font-size:11.5px}
.copy .hl{color:#3c8ee8}
</style>
</head>
<body>
<div class="page">

  <!-- hero photo -->
  <div class="abs hero-photo" role="img" aria-label="Industrial worker in hard hat grinding metal with sparks flying in a dark factory"></div>
  <div class="abs" style="left:0;top:0;width:1200px;height:125px;background:#000"></div>

  <!-- header -->
  <div class="abs topbar"></div>
  <div class="abs topbar-item" style="left:445px"><span class="ico"><svg width="12" height="10" viewBox="0 0 12 10"><rect x=".5" y=".5" width="11" height="9" fill="none" stroke="#fff"/><path d="M.5 .5 6 5l5.5-4.5" fill="none" stroke="#fff"/></svg></span>info@brightformbeam.com</div>
  <div class="abs topbar-item" style="left:642px;font-size:12px"><span class="ico"><svg width="10" height="13" viewBox="0 0 10 13"><path d="M5 12S1 7 1 4.5a4 4 0 0 1 8 0C9 7 5 12 5 12z" fill="#fff"/><circle cx="5" cy="4.5" r="1.5" fill="#1a6fc4"/></svg></span>25 Beam ipsum 0612</div>
  <div class="abs search">Search.....<span class="btn"></span></div>

  <div class="abs logo"><span class="mark"></span>BBSA</div>
  <nav>
    <a class="abs nav" style="left:410px">Home</a>
    <a class="abs nav" style="left:502px">About</a>
    <a class="abs nav" style="left:601px">Why Laser</a>
    <a class="abs nav" style="left:724px">Capabilities</a>
    <a class="abs nav" style="left:856px">ContactUs</a>
  </nav>
  <a class="abs quote">Quote Form</a>

  <!-- hero -->
  <h1 class="abs hero-title">WELCOME TO<br>BRIGHTFORM BEAM<br>SERVICES AUSTRALIA</h1>
  <p class="abs hero-text">Lorem ipsum dolor sit amet, consectetur adipiscing elit, sed do eiusmod tempor incididunt ut labore et dolore magna aliqua.</p>
  <a class="abs btn-grad hero-btn">Get Started</a>

  <svg class="abs hero-cut" width="1200" height="190" viewBox="0 0 1200 190">
    <polygon points="0,0 593,170 1200,0 1200,190 0,190" fill="#050505"/>
    <polygon points="0,14 593,170 593,155 0,0" fill="#e8262f"/>
    <polygon points="593,170 1156,12 1200,12 593,155" fill="#e8262f"/>
    <circle cx="593" cy="150" r="22" fill="#1a6fc4"/>
  </svg>

  <!-- why choose laser -->
  <h2 class="abs sec-title" style="top:874px">WHY CHOOSE LASER</h2>
  <div class="abs sec-dot" style="left:596px;top:925px"></div>
  <div class="abs vert down" style="left:1116px;top:885px;font-size:48px;height:120px;overflow:hidden">LASER</div>

  <div class="abs why-card" style="left:0">
    <svg class="icon-ring" viewBox="0 0 54 54"><circle cx="27" cy="27" r="23" fill="none" stroke="#1a6fc4" stroke-width="4"/><path d="M27 4a23 23 0 0 1 0 46" fill="none" stroke="#e8262f" stroke-width="4"/><path d="M27 14v14l8 5" fill="none" stroke="#e8262f" stroke-width="3" stroke-linecap="round"/></svg>
    <h3>Minimum<br>Downtime</h3>
  </div>
  <div class="abs why-card" style="left:244px">
    <svg class="icon-ring" viewBox="0 0 54 54"><polygon points="27,4 52,50 2,50" fill="#e8262f"/><polygon points="2,50 27,4 27,50" fill="#1a6fc4"/><path d="M18 44c0-6 4-6 4-12M27 44c0-6 4-6 4-12M36 44c0-6 4-6 4-12" fill="none" stroke="#fff" stroke-width="2"/></svg>
    <h3>No Surface<br>Damage</h3>
  </div>
  <div class="abs why-card active" style="left:488px;width:224px">
    <svg class="icon-ring" viewBox="0 0 54 54"><circle cx="27" cy="27" r="24" fill="none" stroke="#fff" stroke-width="3"/><rect x="21" y="14" width="12" height="26" rx="3" fill="none" stroke="#fff" stroke-width="2.5"/><line x1="10" y1="10" x2="44" y2="44" stroke="#fff" stroke-width="3"/></svg>
    <h3>No<br>Environmental</h3>
    <p>Lorem ipsum dolor sit amet, consectetur adipiscing elit, sed do eiusmod tempor incididunt ut labore et dolore magna</p>
  </div>
  <div class="abs why-card" style="left:732px">
    <svg class="icon-ring" viewBox="0 0 54 54"><circle cx="27" cy="27" r="23" fill="none" stroke="#1a6fc4" stroke-width="4"/><path d="M27 4a23 23 0 0 1 0 46" fill="none" stroke="#e8262f" stroke-width="4"/><path d="M27 14v14l8 5" fill="none" stroke="#e8262f" stroke-width="3" stroke-linecap="round"/></svg>
    <h3>No<br>Mess</h3>
  </div>
  <div class="abs why-card" style="left:976px">
    <svg class="icon-ring" viewBox="0 0 54 54"><circle cx="27" cy="27" r="23" fill="none" stroke="#1a6fc4" stroke-width="4"/><path d="M27 4a23 23 0 0 1 0 46" fill="none" stroke="#e8262f" stroke-width="4"/><path d="M27 14v14l8 5" fill="none" stroke="#e8262f" stroke-width="3" stroke-linecap="round"/></svg>
    <h3>No<br>Waste</h3>
  </div>

  <!-- about -->
  <section>
    <div class="abs about-bg"></div>
    <div class="abs vert up" style="left:33px;top:1516px;font-size:48px">ABOUT US</div>
    <div class="abs" style="left:100px;top:1407px;width:242px;height:078px;border-left:4px solid var(--blue);border-top:4px solid var(--blue);height:078px"></div>
    <div class="abs" style="left:100px;top:1407px;width:4px;height:78px;background:var(--blue)"></div>
    <div class="abs about-frame-red"></div>
    <div class="abs about-photo" role="img" aria-label="Three workers in hard hats and high-visibility vests standing with arms crossed in a factory"></div>
    <h2 class="abs about-title">ABOUT BRIGHTFORM BEAM<br>SERVICES AUSTRALIA</h2>
    <p class="abs about-text">Brightform Beam Services Australia (BBSA) is a leading provider of advanced laser restoration services for the residential, commercial, medical, hazardous and industrial sectors, offering waste free, chemical free and damage free complete restoration of metals, concrete, wood, stone and heritage, hygiene and hazard surfaces, with complete removal of coatings, bacteria, paint, rust, graffiti, mold and fire ash (soot), and preparation and treating for welding and bonding.</p>
    <a class="abs btn-grad about-btn">Read More</a>
  </section>

  <!-- contaminants -->
  <section>
    <div class="abs cont-bg"></div>
    <div class="abs sec-dot" style="left:596px;top:2035px"></div>
    <h2 class="abs sec-title" style="top:2056px">WE CLEAN CONTAMINANTS LIKE</h2>
    <div class="abs vert down" style="left:1118px;top:2027px;font-size:44px">CONTAMINANTS</div>

    <div class="abs arrow" style="left:103px;top:2241px"><svg width="8" height="8" viewBox="0 0 8 8"><path d="M5.5 1 2.5 4l3 3" fill="none" stroke="#000" stroke-width="1.6"/></svg></div>
    <div class="abs arrow" style="left:1077px;top:2241px"><svg width="8" height="8" viewBox="0 0 8 8"><path d="M2.5 1l3 3-3 3" fill="none" stroke="#000" stroke-width="1.6"/></svg></div>

    <div class="abs cont-hex hex" style="left:183px"><div class="inner hex" role="img" aria-label="Microscopic view of blue rod-shaped bacteria" style="background:radial-gradient(circle at 40% 40%,#7fb6e8,#1f4f8c 70%,#0d2345)"></div></div>
    <div class="abs cont-hex hex" style="left:511px"><div class="inner hex" role="img" aria-label="Rusted metal surface with flaking orange corrosion" style="background:radial-gradient(circle at 50% 55%,#b8612a,#7a4a2a 50%,#4f6a7a 100%)"></div></div>
    <div class="abs cont-hex hex" style="left:840px"><div class="inner hex" role="img" aria-label="Technician in hard hat inspecting corroded industrial equipment" style="background:linear-gradient(160deg,#d9872a,#b2401f 55%,#3d3f46)"></div></div>

    <div class="abs cont-label" style="left:162px">Bacteria</div>
    <div class="abs cont-label" style="left:490px">Rust</div>
    <div class="abs cont-label" style="left:826px">Corrosion</div>
  </section>

  <!-- surfaces -->
  <section>
    <div class="abs" style="left:0;top:2475px;width:1200px;height:755px;background:#0f1013"></div>
    <div class="abs vert up" style="left:33px;top:2703px;font-size:48px">SURFACES</div>
    <div class="abs sec-dot" style="left:110px;top:2582px"></div>
    <h2 class="abs surf-title">SURFACES</h2>
    <a class="abs view-more">View More</a>

    <div class="abs surf-card" style="left:105px;width:422px;background:radial-gradient(ellipse 200px 140px at 260px 300px,rgba(255,220,150,.7),transparent),linear-gradient(160deg,#1e2a30,#0a0d10)" role="img" aria-label="Welder in protective mask working on metal with bright sparks"></div>
    <div class="abs surf-card" style="left:565px;width:420px;background:linear-gradient(180deg,#e8323a,#d8262f)" role="img" aria-label="Factory floor with engine parts and components under red overlay">
      <svg style="position:absolute;left:201px;top:175px" width="18" height="18" viewBox="0 0 18 18"><path d="M9 2v14M2 9h14" stroke="#fff" stroke-width="2.5"/></svg>
    </div>
    <div class="abs surf-card" style="left:1028px;width:172px;border-radius:0 0 0 26px;background:linear-gradient(120deg,#3b4852,#9aa6ad 40%,#2a3238 70%,#7d8a92)" role="img" aria-label="Close-up of metal wrenches and tools"></div>

    <div class="abs surf-label" style="left:105px;width:422px">Metals <svg width="16" height="16" viewBox="0 0 16 16"><circle cx="8" cy="8" r="8" fill="#fff"/><path d="M4 8h7M8 4.5 11.5 8 8 11.5" fill="none" stroke="#0f1013" stroke-width="2"/></svg></div>
    <div class="abs surf-label" style="left:565px;width:420px">Engines/Parts/Components <svg width="16" height="16" viewBox="0 0 16 16"><circle cx="8" cy="8" r="8" fill="#fff"/><path d="M4 8h7M8 4.5 11.5 8 8 11.5" fill="none" stroke="#0f1013" stroke-width="2"/></svg></div>
    <div class="abs surf-line" style="left:103px;width:425px"></div>
    <div class="abs surf-line" style="left:563px;width:424px"></div>
    <div class="abs surf-line" style="left:1026px;width:174px"></div>
  </section>

  <!-- industries -->
  <section>
    <div class="abs ind-bg"></div>
    <div class="abs sec-dot" style="left:596px;top:3322px"></div>
    <h2 class="abs sec-title" style="top:3348px">INDUSTRIES WE SERVE</h2>
    <div class="abs vert down" style="left:1116px;top:3345px;font-size:46px">INDUSTRIES</div>

    <div class="abs arrow" style="left:103px;top:3504px"><svg width="8" height="8" viewBox="0 0 8 8"><path d="M5.5 1 2.5 4l3 3" fill="none" stroke="#000" stroke-width="1.6"/></svg></div>
    <div class="abs arrow" style="left:1077px;top:3504px"><svg width="8" height="8" viewBox="0 0 8 8"><path d="M2.5 1l3 3-3 3" fill="none" stroke="#000" stroke-width="1.6"/></svg></div>

    <div class="abs ind-hex hex" style="left:140px"><div class="inner hex"><svg width="64" height="64" viewBox="0 0 64 64"><defs><linearGradient id="g1" x1="0" x2="1"><stop offset="0" stop-color="#1a6fc4"/><stop offset="1" stop-color="#e8262f"/></linearGradient></defs><circle cx="32" cy="32" r="30" fill="url(#g1)"/><path d="M27 16h10v11h11v10H37v11H27V37H16V27h11z" fill="#111"/></svg></div></div>
    <div class="abs ind-hex hex" style="left:340px"><div class="inner hex"><svg width="56" height="50" viewBox="0 0 56 50"><path d="M8 32a20 20 0 0 1 40 0z" fill="#e8262f"/><rect x="4" y="34" width="48" height="5" fill="#1a6fc4"/><circle cx="28" cy="10" r="3" fill="#e8262f"/><path d="M10 44h30l8-5" fill="none" stroke="#1a6fc4" stroke-width="3"/></svg></div></div>
    <div class="abs ind-hex hex" style="left:541px"><div class="inner hex"><svg width="56" height="62" viewBox="0 0 56 62"><rect x="28" y="22" width="22" height="28" fill="#e8262f" transform="rotate(-12 39 36)"/><circle cx="39" cy="36" r="5" fill="#fff"/><circle cx="16" cy="10" r="6" fill="#1a6fc4"/><path d="M10 18h12l4 18-6 2v20h-5V40h-4v18H6V36z" fill="#1a6fc4"/></svg></div></div>
    <div class="abs ind-hex hex" style="left:742px"><div class="inner hex"><svg width="60" height="60" viewBox="0 0 60 60"><circle cx="30" cy="34" r="20" fill="none" stroke="#1a6fc4" stroke-width="6" stroke-dasharray="6 4"/><path d="M14 26a16 16 0 0 1 32 0z" fill="#e8262f"/><rect x="10" y="26" width="40" height="4" fill="#e8262f"/><path d="M20 36a10 10 0 0 0 20 0z" fill="#1a6fc4"/></svg></div></div>
    <div class="abs ind-hex hex" style="left:941px"><div class="inner hex"><svg width="60" height="56" viewBox="0 0 60 56"><rect x="6" y="20" width="10" height="22" fill="#1a6fc4"/><rect x="18" y="8" width="12" height="34" fill="#e8262f"/><rect x="32" y="14" width="10" height="28" fill="#1a6fc4"/><rect x="44" y="4" width="10" height="38" fill="#e8262f"/><path d="M4 46h52" stroke="#1a6fc4" stroke-width="4"/><path d="M10 52h40" stroke="#e8262f" stroke-width="3"/></svg></div></div>

    <div class="abs ind-label" style="left:99px">Medical/Sterile</div>
    <div class="abs ind-label" style="left:299px">Hospitality</div>
    <div class="abs ind-label" style="left:500px">Bio Hazardous</div>
    <div class="abs ind-label" style="left:701px">Construction</div>
    <div class="abs ind-label" style="left:900px">Infrastructure</div>
  </section>

  <!-- footer -->
  <footer>
    <div class="abs foot-bg" role="img" aria-label="Dark city skyline at dusk behind the footer"></div>
    <svg class="abs" style="left:0;top:3760px" width="1200" height="160" viewBox="0 0 1200 160">
      <polygon points="0,0 1200,0 1200,148 593,20 0,148" fill="#0d0e11"/>
      <polygon points="0,134 593,18 593,36 0,150" fill="#e8262f"/>
      <polygon points="593,18 1200,134 1200,150 593,36" fill="#e8262f"/>
      <circle cx="593" cy="20" r="22" fill="#1a6fc4"/>
    </svg>
    <div class="abs foot-logo">BBSA</div>
    <nav class="abs foot-nav">
      <a>Home</a><span class="sep">|</span><a>About</a><span class="sep">|</span><a>Why Laser</a><span class="sep">|</span><a>Capabilities</a><span class="sep">|</span><a>ContactUs</a>
    </nav>
    <span class="abs social" style="left:546px"></span>
    <span class="abs social" style="left:588px"></span>
    <span class="abs social" style="left:630px"></span>
    <p class="abs copy">Copyright © 2023 <span class="hl">Brightform Beam Services Australia</span> | All Rights Reserved</p>
  </footer>

</div>
</body>
</html>
```